Calvanto Group Real Estate Company business cards

New business card design, we are generally happy with the basic layout of the existing front of business card, (feel free to change) but require a head shot photo on the back side.

http://www.calvanto.com.au/

Attached logos, and existing business card

------------------------------

Target Market(s)

Real estate

Industry/Entity Type

Real Estate

Contact Information for Business Card

Standard size double sided

Font styles to use
Other font styles liked:
• Futura

Requirements
Must have
• Photo head shot on the back side
Nice to have
• yes
Should not have
• No

```html
<!DOCTYPE html>
<html lang="en">
<head>
<meta charset="utf-8">
<title>Calvanto Group – Business Cards</title>
<link href="https://fonts.googleapis.com/css2?family=Open+Sans:wght@400;600;700&family=Roboto+Condensed:wght@700&display=swap" rel="stylesheet">
<style>
  :root {
    --bg: #3a3a3a;
    --card-white: #f7f7f7;
    --purple: #2d1e5f;
    --purple-text: #2b1d5c;
    --orange: #f0891f;
    --grey-text: #4a4a4a;
    --white: #ffffff;
  }
  * { margin: 0; padding: 0; box-sizing: border-box; }
  html, body { width: 1200px; height: 750px; overflow: hidden; }
  body {
    background: var(--bg);
    font-family: "Open Sans", Arial, sans-serif;
    position: relative;
  }
  .card {
    position: absolute;
    top: 228px;
    width: 461px;
    height: 262px;
    overflow: hidden;
  }
  .card-front { left: 124px; background: var(--card-white); }
  .card-back { left: 618px; background: var(--purple); }

  .brand-name {
    position: absolute;
    left: 30px; top: 30px;
    font-size: 38px;
    font-weight: 600;
    color: var(--purple-text);
    letter-spacing: -0.5px;
    line-height: 1;
  }
  .tagline {
    position: absolute;
    left: 76px; top: 86px;
    font-family: "Roboto Condensed", "Arial Narrow", sans-serif;
    font-weight: 700;
    font-size: 12px;
    color: var(--purple-text);
    word-spacing: 3px;
  }
  .company {
    position: absolute;
    left: 30px; top: 126px;
    font-size: 13px;
    color: var(--grey-text);
    line-height: 18px;
  }
  .company-name { font-weight: 600; }
  .contacts {
    position: absolute;
    left: 30px; top: 168px;
    list-style: none;
    font-size: 12px;
    color: var(--grey-text);
  }
  .contacts li {
    display: flex; align-items: center;
    height: 18px;
  }
  .contacts svg { width: 12px; height: 12px; margin-right: 6px; fill: var(--purple-text); }
  .person {
    position: absolute;
    right: 29px; top: 156px;
    text-align: right;
  }
  .person-name {
    font-size: 20px; font-weight: 600;
    color: var(--purple-text);
    line-height: 24px;
  }
  .person-role {
    font-size: 15px;
    color: var(--orange);
    line-height: 18px;
  }
  .rule-orange {
    position: absolute; left: 0; right: 0; top: 240px;
    height: 2px; background: var(--orange);
  }
  .band-purple {
    position: absolute; left: 0; right: 0; top: 244px; bottom: 0;
    background: var(--purple);
  }

  .headshot {
    position: absolute;
    left: 38px; top: 12px;
    width: 180px; height: 250px;
    background: linear-gradient(180deg, #3b3350 0%, #2a3556 55%, #1f2a48 100%);
  }
  .back-brand {
    position: absolute;
    left: 268px; top: 150px;
    width: 160px;
    text-align: center;
    font-size: 36px;
    font-weight: 600;
    color: var(--orange);
    line-height: 1;
  }
  .back-url {
    position: absolute;
    left: 262px; top: 230px;
    width: 172px;
    text-align: center;
    font-size: 12.5px;
    letter-spacing: 1.2px;
    color: var(--white);
  }
</style>
</head>
<body>
  <section class="card card-front">
    <div class="brand-name">calvanto</div>
    <div class="tagline">Buy &nbsp;|&nbsp; Sell &nbsp;|&nbsp; Rent</div>
    <div class="company">
      <div class="company-name">Calvanto Group</div>
      <div class="company-abn">ABN: 51 824 603 197</div>
    </div>
    <ul class="contacts">
      <li>
        <svg viewBox="0 0 24 24" aria-hidden="true"><path d="M6.6 10.8a15.1 15.1 0 0 0 6.6 6.6l2.2-2.2c.3-.3.7-.4 1-.2 1.1.4 2.3.6 3.6.6.6 0 1 .4 1 1V20c0 .6-.4 1-1 1A17 17 0 0 1 3 4c0-.6.4-1 1-1h3.5c.6 0 1 .4 1 1 0 1.3.2 2.5.6 3.6.1.3 0 .7-.2 1z"/></svg>
        0412 555 308
      </li>
      <li>
        <svg viewBox="0 0 24 24" aria-hidden="true"><circle cx="12" cy="12" r="10"/><path d="M2 12h20M12 2c3 3 3 17 0 20M12 2c-3 3-3 17 0 20" stroke="#f7f7f7" stroke-width="1.6" fill="none"/></svg>
        www.calvanto.com.au
      </li>
      <li>
        <svg viewBox="0 0 24 24" aria-hidden="true"><path d="M2 5h20v14H2z"/><path d="M2 5l10 8 10-8" stroke="#f7f7f7" stroke-width="1.8" fill="none"/></svg>
        daniel.tran@calvanto.com.au
      </li>
    </ul>
    <div class="person">
      <div class="person-name">Daniel Tran</div>
      <div class="person-role">Director</div>
    </div>
    <div class="rule-orange"></div>
    <div class="band-purple"></div>
  </section>

  <section class="card card-back">
    <div class="headshot" role="img" aria-label="Head-and-shoulders photo of the director in a navy suit and blue tie"></div>
    <div class="back-brand">calvanto</div>
    <div class="back-url">www.calvanto.com.au</div>
  </section>
</body>
</html>
```